New business card for a regional office of a US M&A company

We need business card for a finance company, office based in Hong Kong , our Head office is in US, our business is to Merge and acquires companies , the new office will be a regional office for the Asia Pacific region. We want to use the head office logo as attached ( but don't have to be exactly the same, can be a variation to it) as a base and then add Asia Pacific alongside the logo.
We would prefer to have be bilingual Eng + Chinese, although we don't really have Chinese company name .

Industry/Entity Type

Business

Contact Information for Business Card

Clara Jo Tsang
 

VP,
APAC M&A Operations
Orin Vantage Asia Pacific Limited
 
Unit 1407, K18
18 Tai Lok Shan Road, 
Hong Kong 
 
M: +852 6038 1742
T : +852 2836 4100
F : +852 2836 4177
VOIP: 4158
 
cjtsang@orinvantage.com

Font styles to use
Serif
Sans Serif

Colors

Designer to choose colors to be used in the design.

Requirements
Must have
• APAC Office

```html
<!DOCTYPE html>
<html lang="en">
<head>
<meta charset="utf-8">
<title>Orin Vantage Asia Pacific – Business Card</title>
<link rel="stylesheet" href="https://fonts.googleapis.com/css2?family=Open+Sans:wght@400;600;700&family=Arimo:wght@400;700&display=swap">
<style>
  :root {
    --stage: #7d7d7d;
    --paper: #ffffff;
    --navy: #0e2a47;
    --navy-soft: #1b3a5a;
    --teal: #1aa3d0;
    --ink: #333a40;
  }
  * { box-sizing: border-box; margin: 0; padding: 0; }
  html, body { width: 1200px; height: 900px; overflow: hidden; }
  body { background: var(--stage); position: relative; font-family: "Open Sans", sans-serif; }

  .card { position: absolute; top: 306px; width: 439px; height: 271px; }
  .card--front { left: 149px; background: var(--paper); }
  .card--back { left: 609px; width: 440px; background: var(--navy); }

  .brand { position: absolute; left: 27px; top: 22px; display: flex; align-items: center; gap: 12px; }
  .brand__mark { width: 54px; height: 54px; background: var(--navy); }
  .brand__name { font-family: "Open Sans", sans-serif; font-weight: 700; color: var(--navy); font-size: 22px; line-height: 23px; letter-spacing: 0.2px; }

  .voip { position: absolute; right: 23px; top: 40px; font-family: "Arimo", sans-serif; font-size: 13px; color: var(--ink); }
  .voip__label { color: var(--teal); }

  .person { position: absolute; left: 28px; top: 133px; }
  .person__name { font-family: "Arimo", sans-serif; font-weight: 700; font-size: 15px; color: var(--navy); letter-spacing: 0.2px; }
  .person__role { font-size: 11.5px; color: var(--ink); margin-top: 1px; }

  .contact { position: absolute; right: 23px; top: 133px; text-align: right; font-size: 11.5px; color: var(--ink); line-height: 17px; }

  .office { position: absolute; left: 0; right: 0; top: 210px; text-align: center; font-size: 11.5px; line-height: 16.5px; color: var(--ink); }
  .office__company { font-family: "Arimo", sans-serif; font-size: 13px; color: var(--navy); letter-spacing: 0.3px; }
  .office__web { color: var(--teal); }

  .back-pattern { position: absolute; inset: 0; background: linear-gradient(135deg, #163354, #0e2a47); }
  .back-brand { position: absolute; left: 286px; top: 156px; width: 104px; display: flex; flex-direction: column; align-items: center; gap: 6px; }
  .back-brand__mark { width: 30px; height: 30px; background: var(--paper); }
  .back-brand__name { font-weight: 700; font-size: 12px; color: var(--paper); letter-spacing: 0.5px; text-align: center; line-height: 14px; }
</style>
</head>
<body>
  <section class="card card--front">
    <div class="brand">
      <div class="brand__mark"></div>
      <div class="brand__name">ORIN VANTAGE<br>ASIA PACIFIC</div>
    </div>
    <p class="voip"><span class="voip__label">VOIP:</span> 4158</p>

    <div class="person">
      <p class="person__name">CLARA JO TSANG VP</p>
      <p class="person__role">APAC M&amp;A Operations</p>
    </div>
    <div class="contact">
      <p>+852 2836 4100</p>
      <p>cjtsang@orinvantage.com</p>
    </div>

    <div class="office">
      <p class="office__company">ORIN VANTAGE ASIA PACIFIC LTD</p>
      <p>Unit 1407, K18 18 Tai Lok Shan Road, Hong Kong</p>
      <p class="office__web">www.orinvantage.com</p>
    </div>
  </section>

  <section class="card card--back">
    <div class="back-pattern" role="img" aria-label="Repeating pattern of the company mark in muted blue on navy"></div>
    <div class="back-brand">
      <div class="back-brand__mark"></div>
      <p class="back-brand__name">ORIN VANTAGE</p>
    </div>
  </section>
</body>
</html>
```